Copperleaf Roofing Business Card

This is my current business card. But I’d like to make some changes. Somewhere on the card I’d like to list some of the services we offer. Maybe on the back? But I’d still like to keep the red. White and black modern look.

-residential & commercial roofing
-Roof Repairs & Maintenance
-Storm Damage & Insurance Claims specialist
-Christmas Lights and permanent Christmas lights
Fencing. Windows. Gutters. Siding. Sheetrock, painting.

```html
<!DOCTYPE html>
<html lang="en">
<head>
<meta charset="utf-8">
<title>Copperleaf Roofing Co. – Business Card</title>
<link rel="stylesheet" href="https://fonts.googleapis.com/css2?family=Orbitron:wght@700;800&family=Montserrat:wght@400;500&display=swap">
<style>
  :root {
    --red: #e31e24;
    --deep-red: #8e1014;
    --black: #111111;
    --card-dark: #1e1e1e;
    --white: #ffffff;
    --text: #1a1a1a;
    --backdrop: #e9e6e1;
  }
  * { box-sizing: border-box; margin: 0; padding: 0; }
  html, body { width: 900px; height: 1200px; overflow: hidden; }
  body {
    background: var(--backdrop);
    position: relative;
    font-family: "Montserrat", sans-serif;
    color: var(--text);
  }
  .card {
    position: absolute;
    left: 80px;
    width: 742px;
    height: 442px;
    border-radius: 26px;
    overflow: hidden;
    box-shadow: 0 10px 22px rgba(0,0,0,0.25);
  }
  .card--front { top: 130px; background: var(--white); }
  .card--back { top: 638px; background: var(--card-dark); }
  .card__band {
    position: absolute; left: 0; right: 0; bottom: 0; height: 17px;
    background: var(--deep-red);
  }
  .brand-dot {
    position: absolute; border-radius: 50%; background: var(--red);
  }
  .card--front .brand-dot { width: 124px; height: 124px; left: 320px; top: 22px; }
  .card--back .brand-dot { width: 188px; height: 188px; left: 277px; top: 68px; border: 4px solid var(--white); }
  .brand-name {
    position: absolute; left: 0; right: 0; text-align: center;
    font-family: "Orbitron", sans-serif; font-weight: 800; letter-spacing: 1px;
    line-height: 1.15;
  }
  .card--front .brand-name { top: 166px; font-size: 30px; color: var(--red); }
  .card--back .brand-name { top: 278px; font-size: 40px; color: var(--red); }
  .services {
    position: absolute; right: 398px; top: 262px;
    list-style: none; text-align: right; font-size: 16px; line-height: 1.3;
  }
  .services li { position: relative; padding-right: 14px; margin-bottom: 5px; }
  .services li::after {
    content: ""; position: absolute; right: 0; top: 50%;
    width: 6px; height: 6px; margin-top: -3px; border-radius: 50%; background: var(--red);
  }
  .divider {
    position: absolute; left: 365px; top: 260px; width: 2px; height: 142px; background: var(--red);
  }
  .contact { position: absolute; left: 385px; top: 262px; }
  .contact__name {
    font-family: "Orbitron", sans-serif; font-weight: 800; font-size: 24px; letter-spacing: 1px; color: var(--black);
  }
  .contact__name span { color: var(--red); }
  .contact__role { font-size: 16px; margin: 4px 0 10px; }
  .contact__line { display: flex; align-items: center; font-size: 16px; height: 28px; }
  .contact__line svg { width: 16px; height: 16px; margin-right: 8px; fill: var(--red); }
</style>
</head>
<body>
  <section class="card card--front">
    <div class="brand-dot"></div>
    <p class="brand-name">COPPERLEAF<br>ROOFING CO.</p>
    <ul class="services">
      <li>residential &amp; commercial roofing</li>
      <li>Roof Repairs &amp; Maintenance</li>
      <li>Storm Damage &amp;<br>Insurance Claims specialist</li>
      <li>Fencing. Windows. Gutters.<br>Siding. Sheetrock, painting</li>
    </ul>
    <div class="divider"></div>
    <div class="contact">
      <p class="contact__name">DALE <span>MERRITT</span></p>
      <p class="contact__role">Owner</p>
      <p class="contact__line">
        <svg viewBox="0 0 24 24" aria-hidden="true"><path d="M6.6 10.8a15 15 0 0 0 6.6 6.6l2.2-2.2c.3-.3.7-.4 1-.2 1.1.4 2.3.6 3.6.6.6 0 1 .4 1 1V20c0 .6-.4 1-1 1A17 17 0 0 1 3 4c0-.6.4-1 1-1h3.5c.6 0 1 .4 1 1 0 1.3.2 2.5.6 3.6.1.3 0 .7-.2 1z"/></svg>
        682-555-0143
      </p>
      <p class="contact__line">
        <svg viewBox="0 0 24 24" aria-hidden="true"><path d="M2 5h20v2l-10 6L2 7zm0 4l10 6 10-6v10H2z"/></svg>
        dale@copperleafroofing.com
      </p>
      <p class="contact__line">
        <svg viewBox="0 0 24 24" aria-hidden="true"><path d="M12 2a10 10 0 1 0 0 20 10 10 0 0 0 0-20zm6.9 6h-3a15 15 0 0 0-1.3-3.9A8 8 0 0 1 18.9 8zM12 4c.9 1.2 1.6 2.5 2 4h-4c.4-1.5 1.1-2.8 2-4zM4.3 14a8 8 0 0 1 0-4h3.4a16 16 0 0 0 0 4zm.8 2h3a15 15 0 0 0 1.3 3.9A8 8 0 0 1 5.1 16zm3-8h-3a8 8 0 0 1 4.3-3.9C8.8 5.3 8.4 6.6 8.1 8zM12 20c-.9-1.2-1.6-2.5-2-4h4c-.4 1.5-1.1 2.8-2 4zm2.3-6H9.7a14 14 0 0 1 0-4h4.6a14 14 0 0 1 0 4zm.3 5.9c.6-1.2 1-2.5 1.3-3.9h3a8 8 0 0 1-4.3 3.9zm1.7-5.9a16 16 0 0 0 0-4h3.4a8 8 0 0 1 0 4z"/></svg>
        www.copperleafroofing.com
      </p>
    </div>
    <div class="card__band"></div>
  </section>

  <section class="card card--back">
    <div class="brand-dot"></div>
    <p class="brand-name">COPPERLEAF<br>ROOFING CO.</p>
    <div class="card__band"></div>
  </section>
</body>
</html>
```